Expedition Cruise Sales Website for the Polar Regions (Antarctica & Arctic)

This will be a website for selling cruises.
This site should have a homepage, a ship page, destinations, and itineraries.
I have created a file specifying each page, and it is attached.
Pages:
1. Home
2. Cruise Lines
- 2.1 Ships
3. Destinations
- 3.1 Region - 3.2 Country - 3.3 City
4. Itineraries
- 4.1 Itinerary
5. Blog / Travel Tips 6. About Us
7. Contact
Please take a look on the attached pdf
Target Market(s)
Expedition Travelers
Coding
Coded - Design and coding required
Number of Pages Required
5+ page
Font styles to use
Look and feel
Each slider illustrates characteristics of the customer's brand and the style your logo design should communicate.

```html
<!DOCTYPE html>
<html lang="en">
<head>
<meta charset="utf-8">
<title>Travel Tips – Borealis.co</title>
<link href="https://fonts.googleapis.com/css2?family=Figtree:wght@400;500;600;700&display=swap" rel="stylesheet">
<style>
:root{
  --blue:#3a78bf;
  --blue-soft:#cddcec;
  --navy:#0f1d3d;
  --ink:#1b2a4a;
  --text:#2b3245;
  --muted:#8a8f9c;
  --line:#d9dde3;
  --white:#ffffff;
}
*{margin:0;padding:0;box-sizing:border-box}
html,body{width:1200px;height:3229px;overflow:hidden}
body{position:relative;background:var(--white);font-family:'Figtree',sans-serif;color:var(--text)}
.abs{position:absolute}
a{color:inherit;text-decoration:none}

/* hero */
.hero{left:0;top:0;width:1200px;height:312px;background:linear-gradient(100deg,#2f4a2c 0%,#3d5a48 22%,#5b6d78 40%,#3f6f93 60%,#2e628c 100%)}
.hero::after{content:"";position:absolute;inset:0;background:rgba(14,28,60,.45)}
.nav{left:0;top:0;width:1200px;height:100px;z-index:2}
.logo{display:flex;align-items:center;gap:10px;color:var(--white);font-weight:600;font-size:28px}
.logo-dot{width:34px;height:34px;border-radius:50%;background:var(--white)}
.nav .logo{position:absolute;left:65px;top:31px}
.menu{position:absolute;left:378px;top:42px;display:flex;gap:37px;font-size:10px;color:var(--white)}
.menu .active{color:#5b9be0}
.nav-phone{position:absolute;left:906px;top:40px;font-size:12px;color:var(--white);font-weight:500;display:flex;gap:5px;align-items:center}
.btn-book{position:absolute;left:1026px;top:34px;width:99px;height:30px;background:var(--blue);color:var(--white);font-size:10px;font-weight:500;display:flex;align-items:center;justify-content:center}
.hero-title{left:0;width:1200px;top:134px;text-align:center;color:var(--white);font-size:41px;font-weight:600;z-index:2}
.crumbs{left:0;width:1200px;top:192px;text-align:center;color:var(--white);font-size:11px;z-index:2}
.crumbs b{font-weight:600;margin-left:12px}
.crumbs span{margin-left:12px}

/* article */
.meta{left:200px;top:363px;display:flex;align-items:center;font-size:9px;color:var(--ink)}
.tag{border:1px solid var(--ink);padding:3px 6px}
.meta .item{display:flex;align-items:center;gap:5px;margin-left:24px}
.meta .date{color:var(--blue)}
.meta .sep{width:1px;height:11px;background:var(--line);margin-left:12px;margin-right:-12px}
.post-title{left:204px;top:406px;width:500px;font-size:23px;line-height:26px;font-weight:600;color:var(--ink)}
.img-main{left:200px;top:489px;width:800px;height:324px;background:linear-gradient(160deg,#1e6fa8 0%,#3e8f6a 40%,#47a6c4 70%,#2c7a9e 100%)}
.para{left:200px;width:800px;font-size:9.4px;line-height:15px;color:var(--text)}
.sub{left:200px;top:921px;font-size:15px;font-weight:600;color:var(--ink)}
.img-couple{left:200px;top:1075px;width:387px;height:279px;background:linear-gradient(180deg,#aac3d6 0%,#d8c2b4 50%,#8b6b52 100%)}
.img-bay{left:612px;top:1075px;width:388px;height:279px;background:linear-gradient(160deg,#5f8b58 0%,#3eb3c9 45%,#1c6f96 100%)}
.share{left:200px;top:1386px;width:800px;height:50px;border-top:1px solid var(--line);border-bottom:1px solid var(--line);display:flex;align-items:center;padding-left:18px;gap:8px;font-size:9px;color:var(--ink);font-weight:500}
.share .label{margin-right:4px}
.circle{width:31px;height:31px;border-radius:50%;border:1px solid var(--ink);display:flex;align-items:center;justify-content:center}
.circle i{width:8px;height:8px;border-radius:50%;background:currentColor;display:block}

/* reply */
.reply-title{left:0;width:1200px;top:1486px;text-align:center;font-size:15px;font-weight:600;color:var(--ink)}
.reply-note{left:0;width:1200px;top:1511px;text-align:center;font-size:9px;color:var(--ink)}
.field{border-bottom:1px solid var(--line);font-size:10px;color:var(--muted);padding-left:12px}
.btn-post{left:532px;top:1688px;width:136px;height:30px;background:var(--blue);color:var(--white);font-size:10px;font-weight:500;display:flex;align-items:center;justify-content:center}

/* related */
.related-bg{left:262px;top:1768px;width:675px;height:556px;background:var(--blue-soft)}
.related-title{left:0;width:1200px;top:1817px;text-align:center;font-size:19px;font-weight:600;color:var(--ink)}
.card{top:1872px;width:250px;height:355px;background:var(--white);border:1px solid #e3e6ea}
.card .photo{height:155px;position:relative}
.card .chip{position:absolute;left:7px;top:7px;background:var(--white);font-size:8px;padding:3px 5px;color:var(--ink)}
.card .body{padding:18px 18px 0}
.card .d{font-size:9px;color:var(--blue);font-weight:500}
.card h3{margin-top:12px;width:196px;font-size:12.5px;line-height:14.5px;font-weight:600;color:var(--ink)}
.card p{margin-top:12px;width:210px;font-size:8.5px;line-height:13px;color:var(--muted)}
.card .go{margin-top:16px;width:31px;height:31px;border-radius:50%;background:#c9d9ee;display:flex;align-items:center;justify-content:center}
.dots{left:571px;top:2260px;display:flex;gap:7px}
.dots span{width:9px;height:9px;border-radius:50%;background:#9aa2ad}
.dots .on{background:var(--blue)}

/* newsletter */
.news{left:0;top:2455px;width:1200px;height:425px;background:var(--blue)}
.news-photo{left:706px;top:2399px;width:388px;height:481px;background:linear-gradient(180deg,#e4e6e8 0%,#c9ced3 40%,#3d4048 62%,#a7b3bd 80%,#e9eef2 100%)}
.news-title{left:107px;top:2543px;font-size:30px;line-height:35px;color:var(--white);font-weight:400}
.news-title b{font-weight:600}
.news-sub{left:107px;top:2623px;width:400px;font-size:11.5px;line-height:14px;color:var(--white)}
.input{height:29px;background:var(--white);font-size:9px;color:var(--ink);display:flex;align-items:center;padding-left:14px}
.btn-submit{left:107px;top:2770px;width:99px;height:29px;background:var(--navy);color:var(--white);font-size:10px;font-weight:600;display:flex;align-items:center;justify-content:center}
.chat{left:1057px;top:2855px;width:112px;height:49px;background:var(--white);border-radius:3px;box-shadow:0 2px 6px rgba(0,0,0,.15);padding:12px 0 0 9px;font-size:7px;color:var(--ink);line-height:9px}
.chat strong{font-size:13px;color:var(--blue);font-weight:600}
.chat-dot{left:1123px;top:2837px;width:35px;height:35px;border-radius:50%;background:#3ec45a;border:3px solid var(--white)}

/* footer */
.footer{left:0;top:2880px;width:1200px;height:349px;background:linear-gradient(180deg,#1e2b4d 0%,#243457 60%,#1d2948 100%)}
.f-logo{left:107px;top:2960px;font-size:28px}
.f-logo .logo-dot{width:42px;height:42px}
.f-about{left:107px;top:3015px;width:380px;font-size:9.5px;line-height:19px;color:var(--white)}
.f-h{font-size:13px;font-weight:600;color:var(--white)}
.f-row{font-size:10px;color:var(--white);display:flex;gap:8px;align-items:center}
.f-links{font-size:9px;line-height:18.8px;color:var(--white)}
.f-social{left:588px;top:3079px;display:flex;gap:6px;color:var(--white)}
.f-social .circle{border-color:var(--white)}
.f-rule{left:107px;top:3160px;width:1000px;height:1px;background:rgba(255,255,255,.2)}
.copy{left:107px;top:3192px;font-size:9px;color:var(--white)}
</style>
</head>
<body>

<header>
  <div class="abs hero" role="img" aria-label="Coastal cliffs above a beach with swimmers in turquoise water"></div>
  <nav class="abs nav">
    <a class="logo" href="#"><span class="logo-dot"></span>Borealis.co</a>
    <div class="menu">
      <a class="active" href="#">Home</a><a href="#">Cruise lines</a><a href="#">Destinations</a><a href="#">Itineraries</a><a href="#">Blog</a><a href="#">About us</a><a href="#">Contact</a>
    </div>
    <div class="nav-phone">
      <svg width="10" height="10" viewBox="0 0 24 24" fill="none" stroke="#fff" stroke-width="2"><path d="M22 16.9v3a2 2 0 0 1-2.2 2A19.8 19.8 0 0 1 2.1 4.2 2 2 0 0 1 4.1 2h3a2 2 0 0 1 2 1.7l.5 3a2 2 0 0 1-.6 1.8L7.6 9.9a16 16 0 0 0 6.5 6.5l1.4-1.4a2 2 0 0 1 1.8-.6l3 .5a2 2 0 0 1 1.7 2z"/></svg>
      555.010.2040
    </div>
    <a class="btn-book" href="#">Book Now!</a>
  </nav>
  <h1 class="abs hero-title">Travel Tips</h1>
  <div class="abs crumbs">Home <span>&gt;&gt;</span><b>Blog</b></div>
</header>

<main>
  <div class="abs meta">
    <span class="tag">Travel tips</span>
    <span class="item date">
      <svg width="9" height="9" viewBox="0 0 24 24" fill="none" stroke="#3a78bf" stroke-width="2"><rect x="3" y="5" width="18" height="16"/><path d="M3 10h18M8 3v4M16 3v4"/></svg>June 16, 2025</span>
    <span class="sep"></span>
    <span class="item"><svg width="9" height="9" viewBox="0 0 24 24" fill="none" stroke="#3a78bf" stroke-width="2"><circle cx="12" cy="8" r="4"/><path d="M4 21c0-4 4-6 8-6s8 2 8 6"/></svg>Standard chunk</span>
    <span class="sep"></span>
    <span class="item"><svg width="9" height="9" viewBox="0 0 24 24" fill="none" stroke="#3a78bf" stroke-width="2"><path d="M4 4h16v12H9l-5 4z"/></svg>0 Comments</span>
  </div>

  <h2 class="abs post-title">Lorem ipsum is simply dummy text of the printing and&nbsp; typesetting</h2>

  <div class="abs img-main" role="img" aria-label="Aerial view of a tropical island resort with beaches, lagoon and docked boats"></div>

  <p class="abs para" style="top:846px">Morbi mauris mi, facilisis a tortor pulvinar, cursus pulvinar sapien. etiam pretium libero sit amet massa laoreet ultricies vel a est. orci varius natoque penatibus et magnis dis parturient montes, nascetur ridiculus mus. mauris enim purus, rhoncus vel ligula id, scelerisque gravida eros. quisque fermentum quam at leo aliquam, vitae molestie felis condimentum. duis faucibus magna dapibus diam vestibulum, ac viverra eros fermentum. pellentesque finibus nulla turpis, eu dignissim nibh finibus nec.</p>

  <h3 class="abs sub">Lorem ipsum is simply dummy text of the</h3>

  <p class="abs para" style="top:953px">Maecenas pretium nisl ac metus tempor pharetra. maecenas pulvinar ut arcu nec blandit. nullam quis risus vulputate, rhoncus ligula imperdiet, varius purus. sed vel rutrum ipsum. ut scelerisque tellus id dui aliquam, eget tincidunt ipsum aliquet. ut turpis sapien, aliquam scelerisque feugiat vel, vulputate non lacus. nunc blandit auctor massa id venenatis. vestibulum a blandit dolor. praesent vel laoreet tellus, at mattis neque. mauris sapien odio, gravida finibus erat sit amet, viverra lobortis risus.</p>

  <p class="abs para" style="top:1013px">Integer commodo feugiat nulla ut maximus. proin tincidunt ut mi et dictum. maecenas tempor maximus felis, vitae sollicitudin leo gravida in. nullam sodales vulputate purus. dictum id magna eu sodales. nunc laoreet arcu sed libero facilisis dapibus. sed feugiat nunc vitae mi commodo viverra.</p>

  <div class="abs img-couple" role="img" aria-label="Couple relaxing together on the deck of a sailing yacht at sea"></div>
  <div class="abs img-bay" role="img" aria-label="Sailing yacht anchored in a turquoise bay between rocky cliffs"></div>

  <div class="abs share">
    <span class="label">Share:</span>
    <span class="circle" aria-label="Share on social network one"><i></i></span>
    <span class="circle" aria-label="Share on social network two"><i></i></span>
    <span class="circle" aria-label="Share on social network three"><i></i></span>
    <span class="circle" aria-label="Share on social network four"><i></i></span>
  </div>

  <section>
    <h3 class="abs reply-title">Leave a Reply</h3>
    <p class="abs reply-note">Your email address will not be published. required fields are marked *</p>
    <div class="abs field" style="left:282px;top:1564px;width:311px;height:22px">Your name*</div>
    <div class="abs field" style="left:607px;top:1564px;width:311px;height:22px">Your email*</div>
    <div class="abs field" style="left:282px;top:1608px;width:636px;height:66px">Your name*</div>
    <a class="abs btn-post" href="#">Post Comment</a>
  </section>

  <section>
    <div class="abs related-bg"></div>
    <h2 class="abs related-title">Related Posts</h2>

    <article class="abs card" style="left:200px">
      <div class="photo" role="img" aria-label="Expedition ship among icebergs and snowy mountains" style="background:linear-gradient(180deg,#c9d9ea,#e9eef4 45%,#2f5f93)"><span class="chip">Cruise news</span></div>
      <div class="body"><div class="d">June 16, 2025</div><h3>Lorem ipsum is simply dummy text of the printing and typesetting</h3><p>It is a long established fact that a reader will be distracted by the readable content of a page when looking at its layout.</p><div class="go"><svg width="9" height="9" viewBox="0 0 24 24" fill="none" stroke="#3a78bf" stroke-width="2.5"><path d="M4 12h16M14 6l6 6-6 6"/></svg></div></div>
    </article>

    <article class="abs card" style="left:475px">
      <div class="photo" role="img" aria-label="Snorkeler swimming in clear turquoise water" style="background:linear-gradient(180deg,#6fd0c8,#2bb3b0 50%,#3a8f6e)"><span class="chip">Travel tips</span></div>
      <div class="body"><div class="d">June 16, 2025</div><h3>Lorem ipsum is simply dummy text of the printing and typesetting</h3><p>It is a long established fact that a reader will be distracted by the readable content of a page when looking at its layout.</p><div class="go"><svg width="9" height="9" viewBox="0 0 24 24" fill="none" stroke="#3a78bf" stroke-width="2.5"><path d="M4 12h16M14 6l6 6-6 6"/></svg></div></div>
    </article>

    <article class="abs card" style="left:750px">
      <div class="photo" role="img" aria-label="Large cruise ship sailing past a historic harbour city" style="background:linear-gradient(180deg,#7a8fb0,#c79a6a 40%,#2c4d78)"><span class="chip">Cruise news</span></div>
      <div class="body"><div class="d">June 16, 2025</div><h3>Lorem ipsum is simply dummy text of the printing and typesetting</h3><p>It is a long established fact that a reader will be distracted by the readable content of a page when looking at its layout.</p><div class="go"><svg width="9" height="9" viewBox="0 0 24 24" fill="none" stroke="#3a78bf" stroke-width="2.5"><path d="M4 12h16M14 6l6 6-6 6"/></svg></div></div>
    </article>

    <svg class="abs" style="left:1133px;top:2031px" width="8" height="10" viewBox="0 0 8 10" fill="none" stroke="#6b7280" stroke-width="1.3"><path d="M2 1l4 4-4 4"/></svg>
    <div class="abs dots"><span></span><span class="on"></span><span></span><span></span></div>
  </section>

  <section>
    <div class="abs news"></div>
    <div class="abs news-photo" role="img" aria-label="Expedition cruise ship moored among sea ice below snowy cliffs"></div>
    <h2 class="abs news-title">Get cruise deals <b>directly<br>in your inbox</b></h2>
    <p class="abs news-sub">Subscribe now and set sail on a journey of endless adventure with our exclusive cruise newsletter</p>
    <div class="abs input" style="left:107px;top:2682px;width:233px">First Name</div>
    <div class="abs input" style="left:354px;top:2682px;width:233px">Last Name</div>
    <div class="abs input" style="left:107px;top:2726px;width:233px">Email Address...</div>
    <div class="abs input" style="left:354px;top:2726px;width:233px">Mobile Number</div>
    <a class="abs btn-submit" href="#">Submit</a>
  </section>
</main>

<footer>
  <div class="abs footer"></div>
  <a class="abs logo f-logo" href="#"><span class="logo-dot"></span>Borealis.co</a>
  <p class="abs f-about">Lorem Ipsum is simply dummy text of the printing and typesetting industry. Lorem Ipsum has been the industry's standard dummy text ever since the 1500s, when an unknown printer took a galley of type and scrambled it to make a type specimen book.</p>

  <h4 class="abs f-h" style="left:588px;top:2951px">Contct Us</h4>
  <div class="abs f-row" style="left:588px;top:2981px">
    <svg width="10" height="10" viewBox="0 0 24 24" fill="none" stroke="#fff" stroke-width="2"><path d="M22 16.9v3a2 2 0 0 1-2.2 2A19.8 19.8 0 0 1 2.1 4.2 2 2 0 0 1 4.1 2h3a2 2 0 0 1 2 1.7l.5 3a2 2 0 0 1-.6 1.8L7.6 9.9a16 16 0 0 0 6.5 6.5l1.4-1.4a2 2 0 0 1 1.8-.6l3 .5a2 2 0 0 1 1.7 2z"/></svg>555.010.2040</div>
  <div class="abs f-row" style="left:588px;top:3010px;font-size:9px">
    <svg width="10" height="10" viewBox="0 0 24 24" fill="#fff"><path d="M2 6l10 7 10-7v12H2z"/></svg>help@borealisvoyage.com</div>
  <h4 class="abs f-h" style="left:588px;top:3049px">Follow us</h4>
  <div class="abs f-social">
    <span class="circle"><i></i></span><span class="circle"><i></i></span><span class="circle"><i></i></span><span class="circle"><i></i></span>
  </div>

  <h4 class="abs f-h" style="left:819px;top:2951px">Quick Links</h4>
  <div class="abs f-links" style="left:819px;top:2981px">Home<br>Cruise Lines<br>Destinations<br>Itineraries<br>Blog<br>About Us<br>Contact</div>
  <div class="abs f-links" style="left:924px;top:2981px">FAQ<br>Privacy Policy<br>Terms and Conditions<br>Booking Confirmation</div>

  <div class="abs f-rule"></div>
  <svg class="abs" style="left:1130px;top:3151px" width="16" height="18" viewBox="0 0 16 18" fill="#fff"><path d="M8 0l8 18-8-5-8 5z"/></svg>
  <p class="abs copy">© 2025 <b>Borealis.co</b> All Rights Reserved</p>

  <div class="abs chat"><div>Available</div><strong>24/7</strong> to Assist with<br>Any Questions</div>
  <div class="abs chat-dot" aria-label="Chat"></div>
</footer>

</body>
</html>
```